Nanny Share Ecommerce Website for Finding Childcare and Parents who need Childcare BrightPramHub.net

Our company needs an ecommerce website (BrightPramHub.net) for a US subscription based service strictly for nanny sharing that connects families and caregivers. The website would allow families to connect with one another as well as to search for nannies. The service would be searchable for other families by location (by radius or zip code), children demographic (age range/gender/special needs), days of week or times, after school care, school closure days (holidays), etc. The service would also be searchable for nannies based on gender, provider age range, years experience, language, hourly rate, transportation available, certification (CPR first aid), education etc. The search fields would be searchable and sortable and allow to connect with the provider (after paying subscription fee). The service would be similar to tendlyfolk.net in that it would allow for families and caregivers to post photos as well as a short bio of the themselves. There would also be a feedback/star rating mechanism to rate caregivers who have performed work for families (viewable to public). The service would be free for nannies to post their bios and only a subscription based service for families to connect with other families or with caregivers (able to view bio but need service to connect). There will be a short bio on the benefits of nanny sharing (reduced cost, increased flexibility for parents, reduced illness, increased socialization with other children vs. sole nanny), as well as Q&A section with best practices.

Target Market(s)

Families, Nannies

Industry/Entity Type

Childcare

Logo Text

Bright Pram Hub

Coding

Coded - Design and coding required

Number of Pages Required

5+ page

Requirements
Must have
• Searchable (need to be able to search for families as well as nannies), responsive, functional, easy to use, add value to families and nannies. Needs to be able to collect payment for subscription.
Nice to have
• Optimized for mobile, SEO optimized

```html
<!DOCTYPE html>
<html lang="en">
<head>
<meta charset="utf-8">
<title>Bright Pram Hub – Build Profiles for Nannies</title>
<link href="https://fonts.googleapis.com/css2?family=Montserrat:wght@400;500;600;700&family=Open+Sans:wght@400;600&display=swap" rel="stylesheet">
<style>
  :root {
    --sky: #2ec4f1;
    --pink: #f24b80;
    --ink: #222222;
    --text: #444444;
    --muted: #666666;
    --panel: #f8f8f8;
    --line: #dddddd;
    --footer: #1c1c1c;
    --white: #ffffff;
  }
  * { box-sizing: border-box; margin: 0; padding: 0; }
  html, body { width: 1106px; height: 1200px; overflow: hidden; background: var(--white); }
  body { position: relative; font-family: "Open Sans", sans-serif; color: var(--text); }

  .site-header { position: absolute; top: 0; left: 0; width: 1106px; height: 98px; border-top: 3px solid var(--sky); background: var(--white); }
  .brand { position: absolute; left: 92px; top: 30px; display: flex; align-items: center; gap: 10px; font-family: "Montserrat", sans-serif; font-weight: 700; font-size: 25px; color: var(--ink); }
  .brand-dot { width: 30px; height: 30px; border-radius: 50%; border: 3px solid var(--sky); }
  .main-nav a { position: absolute; top: 40px; font-size: 13.5px; color: var(--text); text-decoration: none; }
  .main-nav a.active { color: var(--sky); }
  .search-icon { position: absolute; left: 1003px; top: 44px; }

  .hero { position: absolute; top: 98px; left: 0; width: 1106px; height: 321px; background: linear-gradient(90deg, #8e8a87 0%, #a6908a 35%, #b98a82 60%, #a9a6a8 100%); }
  .hero-title { position: absolute; left: 0; width: 100%; top: 228px; text-align: center; font-family: "Montserrat", sans-serif; font-weight: 600; font-size: 50px; color: var(--white); letter-spacing: 0.5px; }

  .profile-card { position: absolute; left: 90px; top: 473px; width: 925px; height: 435px; background: var(--panel); border: 1px solid var(--line); }
  .card-title { position: absolute; left: 22px; top: 50px; font-family: "Montserrat", sans-serif; font-weight: 600; font-size: 26px; color: var(--ink); }
  .avatar { position: absolute; left: 42px; top: 116px; }
  .upload-btn { position: absolute; left: 25px; top: 250px; width: 152px; height: 29px; border-radius: 15px; background: var(--pink); color: var(--white); font-family: "Montserrat", sans-serif; font-weight: 600; font-size: 12.5px; text-align: center; line-height: 29px; }

  .field-label { position: absolute; font-size: 15px; color: var(--text); line-height: 30px; }
  .field-input { position: absolute; height: 30px; background: var(--white); border: 1px solid #cfcfcf; }
  .field-select { font-size: 13px; color: var(--text); padding-left: 15px; line-height: 28px; }
  .field-select svg { position: absolute; right: 15px; top: 12px; }

  .bio-text { position: absolute; left: 214px; top: 267px; width: 650px; font-family: "Montserrat", sans-serif; font-size: 12px; line-height: 25px; color: var(--muted); }
  .bio-text .more { color: var(--sky); margin-left: 8px; }
  .build-btn { position: absolute; left: 722px; top: 345px; width: 141px; height: 34px; background: var(--sky); color: var(--white); font-size: 15.5px; font-weight: 600; text-align: center; line-height: 34px; }

  .site-footer { position: absolute; top: 965px; left: 0; width: 1106px; height: 235px; background: var(--footer); border-top: 3px solid var(--sky); }
  .social { position: absolute; top: 59px; left: 430px; display: flex; gap: 4px; }
  .social span { width: 38px; height: 38px; border: 1.5px solid var(--white); border-radius: 50%; }
  .footer-nav { position: absolute; top: 120px; width: 100%; text-align: center; font-size: 14px; color: var(--white); word-spacing: 0; }
  .footer-nav .sep { margin: 0 15px; }
  .copyright { position: absolute; top: 158px; width: 100%; text-align: center; font-size: 11.5px; color: var(--white); }
</style>
</head>
<body>
  <header class="site-header">
    <div class="brand"><span class="brand-dot"></span>Bright Pram Hub</div>
    <nav class="main-nav">
      <a class="active" style="left:446px">Home</a>
      <a style="left:515px">About us</a>
      <a style="left:600px">Services</a>
      <a style="left:681px">How it Works</a>
      <a style="left:792px">FAQ</a>
      <a style="left:849px">Blog</a>
      <a style="left:908px">Contact us</a>
    </nav>
    <svg class="search-icon" width="13" height="13" viewBox="0 0 13 13"><circle cx="5.5" cy="5.5" r="4" fill="none" stroke="#f24b80" stroke-width="2"/><line x1="8.5" y1="8.5" x2="12" y2="12" stroke="#f24b80" stroke-width="2.2" stroke-linecap="round"/></svg>
  </header>

  <section class="hero" role="img" aria-label="Photo of a nanny playing with a little girl and toy blocks">
  </section>
  <h1 class="hero-title">BUILD PROFILES-NANNIES</h1>

  <main class="profile-card">
    <h2 class="card-title">Let’s Start with the basic Information</h2>
    <svg class="avatar" width="118" height="118" viewBox="0 0 118 118" aria-label="Profile photo placeholder">
      <defs><clipPath id="avatar-clip"><circle cx="59" cy="59" r="55"/></clipPath></defs>
      <circle cx="59" cy="59" r="56" fill="#fff" stroke="#111" stroke-width="3"/>
      <g clip-path="url(#avatar-clip)" fill="#111">
        <ellipse cx="59" cy="44" rx="20" ry="24"/>
        <path d="M14 118 C16 88 36 78 59 78 C82 78 102 88 104 118 Z"/>
      </g>
    </svg>
    <div class="upload-btn">Upload your photo</div>

    <span class="field-label" style="left:212px;top:116px">Name</span>
    <div class="field-input" style="left:272px;top:116px;width:244px"></div>
    <span class="field-label" style="left:531px;top:116px">Location</span>
    <div class="field-input" style="left:607px;top:116px;width:295px"></div>

    <span class="field-label" style="left:212px;top:165px">Years of Experience</span>
    <div class="field-input" style="left:365px;top:165px;width:86px"></div>
    <span class="field-label" style="left:467px;top:163px">Age</span>
    <div class="field-input" style="left:508px;top:165px;width:93px"></div>
    <span class="field-label" style="left:622px;top:165px">Available Time</span>
    <div class="field-input field-select" style="left:736px;top:165px;width:166px">Any
      <svg width="8" height="5" viewBox="0 0 8 5"><path d="M1 1 L4 4 L7 1" fill="none" stroke="#444" stroke-width="1.3"/></svg>
    </div>

    <span class="field-label" style="left:212px;top:213px">Pay Rate</span>
    <div class="field-input" style="left:283px;top:213px;width:233px"></div>
    <span class="field-label" style="left:531px;top:213px">Avg Response</span>
    <div class="field-input" style="left:639px;top:213px;width:263px"></div>

    <p class="bio-text">At vero eos et accusamus et iusto odio dignissimos ducimus qui blanditiis praesentium voluptatum deleniti atque corrupti quos dolores et quas molestias excepturi sint occaecati cupiditate non provident, similique sunt in culpa qui officia deserunt mollitia animi, id est laborum <span class="more">......more</span></p>
    <div class="build-btn">BUILD PROFILE</div>
  </main>

  <footer class="site-footer">
    <div class="social"><span></span><span></span><span></span><span></span><span></span><span></span></div>
    <nav class="footer-nav">Home<span class="sep">/</span>About us<span class="sep">/</span>Services<span class="sep">/</span>How it works<span class="sep">/</span>FAQ<span class="sep">/</span>Blog<span class="sep">/</span>Contact us</nav>
    <p class="copyright">© Copyright 2018 Bright Pram Hub.All Rights Reserved</p>
  </footer>
</body>
</html>
```